2 x Digitize Logo | 2 x Business Cards | 2 x Fridge Magnets

We require 6 deliverables:
1. Residential logo redrawn (same just high quality for large print format).
2. Corporate logo redrawn (minor changes to wording and high quality for large print format).
3. New business card design for Furniture Removals (residential)
4. New business card design for Corporate Relocations (business)
5. New Fridge magnet for Furniture removals (residential)
6. New fridge magnet for Corporate Relocations (business)
1. Residential Logo
a. We require the logo to be translated into a high quality digital image with no modifications.
(see attached resilogo.jpg)
2. Residential Logo
a. We require the logo to be edited (add the word corporate relocations) be translated into a high quality digital image.
(see attached corplogo.jpg)
3. Using the resilogo please make a new business card for our business.
a. Please see the web site https://www.larkbendcarters.com.au for colours and inspiration.
b. The residential business card needs the following information:
i. Business Name (using the residential logo).
ii. Free Call: 1800 LB Cart (the L, B and Cart much be the same colour as the logo).
iii. Website: www.LarkbendCarters.com.au
iv. Address: 4/17 Ormsdale Court, VIC 3264
v. Email: cart@LarkbendCarters.com.au
vi. backof Card:
Review our service
www.PennantOrbit.com.au
Services: Local, Country, Interstate | Furniture Removals | Piano, Billiard Tables & Antiques
4. Using the corplogo please make a new business card for our business.
b. The corporate business card needs the following information:
i. Business Name (using the corporate logo).
v. Email: corporate@LarkbendCarters.com.au
vi. Back of Card:
Review our service
www.PennantOrbit.com.au
Services: Corporate relocations | Office equipment moves | Packing Service | Packing Materials
5. Using the resilogo please make a new fridge magent for our business.
b. The residential fidge magnet needs the following information:
iv. Services: Local, Country, Interstate | Furniture Removals | Piano, Billiard Tables & Antiques
6. Using the corplogo please make a new fridge magent for our business.
b. The corporate fidge magnet needs the following information:
iv. Services: Local, Country, Interstate | Corporate relocations
Target Market(s)
Residential Furniture Removals and Corporate Office relocations
Industry/Entity Type
Business
Contact Information for Business Card
Please see full brief for six items required
Requirements
Must have
- Clean simple, easy to read
Nice to have
- fresh, stand out, eye catching
Should not have
- plain, standard, boring, general

```html
<!DOCTYPE html>
<html lang="en">
<head>
<meta charset="utf-8">
<title>Larkbend Carters – Business Cards</title>
<link href="https://fonts.googleapis.com/css2?family=Roboto+Condensed:wght@700&display=swap" rel="stylesheet">
<style>
  :root {
    --ink: #333333;
    --brand-yellow: #fcc72c;
    --brand-red: #e8303a;
    --brand-green: #00a651;
    --paper: #ffffff;
    --rule: #3a3a3a;
  }
  html, body {
    margin: 0;
    padding: 0;
    overflow: hidden;
    background: var(--paper);
  }
  .canvas {
    position: relative;
    width: 1200px;
    height: 1200px;
    box-sizing: border-box;
    border: 1.5px solid var(--rule);
    background: var(--paper);
    font-family: "Roboto Condensed", "Arial Narrow", sans-serif;
    font-weight: 700;
    color: var(--ink);
    overflow: hidden;
  }
  .card {
    position: absolute;
    left: 231px;
    width: 738px;
    height: 554px;
    box-sizing: border-box;
    border: 1.5px solid var(--rule);
    background: var(--paper);
  }
  .card--corporate { top: 36px; }
  .card--residential { top: 610px; }

  .line {
    position: absolute;
    left: 0;
    right: 0;
    margin: 0;
    text-align: center;
    white-space: nowrap;
  }
  .brand-name {
    font-size: 54px;
    line-height: 64px;
    letter-spacing: 0.5px;
    text-transform: uppercase;
  }
  .card--corporate .brand-name { color: var(--brand-red); }
  .card--residential .brand-name { color: var(--brand-green); }
  .brand-dot {
    display: inline-block;
    width: 22px;
    height: 22px;
    border-radius: 50%;
    margin-right: 14px;
    vertical-align: 6px;
  }
  .card--corporate .brand-dot { background: var(--brand-green); }
  .card--residential .brand-dot { background: var(--brand-yellow); }

  .phone {
    font-size: 53px;
    line-height: 60px;
  }
  .phone .l { color: var(--brand-yellow); }
  .phone .b { color: var(--brand-red); }
  .phone .cart { color: var(--brand-green); }

  .website {
    font-size: 32px;
    line-height: 40px;
  }
  .services-title {
    font-size: 30px;
    line-height: 38px;
  }
  .services {
    font-size: 31px;
    line-height: 44px;
  }
</style>
</head>
<body>
<main class="canvas">

  <section class="card card--corporate" aria-label="Corporate relocations business card">
    <p class="line brand-name" style="top:122px;"><span class="brand-dot"></span>Larkbend Carters</p>
    <p class="line phone" style="top:259px;">Free Call: 1800 <span class="l">L</span><span class="b">B</span> <span class="cart">Cart</span></p>
    <p class="line website" style="top:328px;">Website: www.LarkbendCarters.com.au</p>
    <p class="line services-title" style="top:381px;">Services:</p>
    <p class="line services" style="top:440px;">Corporate relocations | Office equipment moves<br>Packing Service | Packing Materials</p>
  </section>

  <section class="card card--residential" aria-label="Furniture removals business card">
    <p class="line brand-name" style="top:98px;"><span class="brand-dot"></span>Larkbend Carters</p>
    <p class="line phone" style="top:256px;">Free Call: 1800 <span class="l">L</span><span class="b">B</span> <span class="cart">Cart</span></p>
    <p class="line website" style="top:328px;">Website: www.LarkbendCarters.com.au</p>
    <p class="line services-title" style="top:381px;">Services:</p>
    <p class="line services" style="top:440px;">Local, Country, Interstate | Furniture Removals<br>Piano, Billiard Tables &amp; Antiques</p>
  </section>

</main>
</body>
</html>
```